Business Cards Design for the electrical wholesaler: clean bold dynamic :)

We need a business card design that would follow our latest brand guidelines. As an electrical wholesaler we want to bring a fresh look and feel into the industry. The design should be clean bold and dynamic. It should come alive with the renewed energy of our green colour. Our grey colour should keep things balanced and complement the notion of maturity and responsibility. We employ Lato as a corporate font however are not bound by this font and we’re open to interpretation here.

Target Market(s)

Electrical contractors

Industry/Entity Type

Business

Contact Information for Business Card

Logo
Name & Surname: Halyna Dorosh
Job Title: Director of Marketing
Email: halya.dorosh@quillmail.example
Cell phone: XXX.XXX.XXXX
Address: 20517 - 87 Ave. Edmonton, AB, Canada. T6K 4N8
Business Phone: 780.555.0184
Website: www.brovix.example

Font styles to use
Other font styles liked:
• Lato

Requirements
Must have
• Logo & website
Nice to have
• Brand elements - some of them you may find in the attached Brand Guidelines (e.g. three lines on the background signifying "W")

```html
<!DOCTYPE html>
<html lang="en">
<head>
<meta charset="utf-8">
<title>brovix business card</title>
<link rel="stylesheet" href="https://fonts.googleapis.com/css2?family=Exo+2:wght@600&family=Lato:wght@400;700&display=swap">
<style>
  :root {
    --backdrop: #3b3b3d;
    --card: #232324;
    --green: #7cc52a;
    --grey: #b9b9b9;
    --white: #f2f2f2;
  }
  * { box-sizing: border-box; margin: 0; padding: 0; }
  html, body {
    width: 799px; height: 1200px; overflow: hidden;
    background: var(--backdrop);
    font-family: "Lato", sans-serif;
  }
  .sheet {
    width: 799px; height: 1200px;
    display: flex; flex-direction: column; align-items: center; justify-content: space-around;
    padding: 60px 0;
  }
  .card {
    width: 580px; height: 340px;
    background: var(--card);
    border-radius: 30px;
    box-shadow: 0 18px 40px rgba(0,0,0,.45);
    position: relative;
  }
  .card-front { display: flex; align-items: center; justify-content: center; }
  .brand { display: flex; flex-direction: column; }
  .brand-line { display: flex; align-items: center; gap: 16px; }
  .brand-dot {
    width: 44px; height: 44px; border-radius: 50%;
    background: var(--green);
  }
  .brand-name {
    font-weight: 700; color: var(--grey);
    font-size: 92px; line-height: 1; letter-spacing: -1px;
  }
  .brand-tag {
    color: var(--green); font-weight: 700;
    font-size: 15px; letter-spacing: 3px; text-transform: uppercase;
    margin-top: 6px; margin-left: 62px;
  }
  .card-back { display: flex; align-items: center; padding: 0 36px; gap: 30px; }
  .card-back .brand { width: 196px; flex: none; margin-top: -40px; }
  .card-back .brand-line { gap: 10px; }
  .card-back .brand-dot { width: 26px; height: 26px; }
  .card-back .brand-name { font-size: 52px; }
  .card-back .brand-tag { font-size: 9px; letter-spacing: 1.6px; margin-left: 36px; color: var(--grey); }
  .contact { color: var(--white); font-size: 14px; line-height: 1.35; min-width: 0; }
  .person-name {
    font-family: "Exo 2", sans-serif; font-weight: 600;
    color: var(--green); font-size: 27px; line-height: 1.1;
  }
  .person-role { font-size: 15px; margin-bottom: 10px; }
  .address { margin-bottom: 6px; }
  .contact-row { display: flex; align-items: center; gap: 8px; margin-top: 4px; white-space: nowrap; }
  .contact-row svg { width: 16px; height: 16px; flex: none; }
</style>
</head>
<body>
<main class="sheet">
  <section class="card card-front">
    <div class="brand">
      <div class="brand-line"><span class="brand-dot"></span><span class="brand-name">brovix</span></div>
      <div class="brand-tag">Electrical Wholesalers</div>
    </div>
  </section>

  <section class="card card-back">
    <div class="brand">
      <div class="brand-line"><span class="brand-dot"></span><span class="brand-name">brovix</span></div>
      <div class="brand-tag">Electrical Wholesalers</div>
    </div>
    <div class="contact">
      <div class="person-name">Halyna Dorosh</div>
      <div class="person-role">Director of Marketing</div>
      <div class="address">20517 - 87 Ave. Edmonton,<br>AB, Canada T6K 4N8</div>
      <div class="contact-row">
        <svg viewBox="0 0 16 16"><circle cx="8" cy="8" r="8" fill="#7cc52a"/><path d="M5 4.5c.5-.5 1-.5 1.3 0l.8 1.3c.2.4 0 .7-.3 1-.3.2-.2.6.2 1.2.5.7.9 1 1.2.8.3-.3.6-.4 1-.2l1.3.8c.5.3.4.8 0 1.3-1 1-3 .2-4.4-1.5C4.8 7.5 4.2 5.4 5 4.5z" fill="#232324"/></svg>
        <span>+1 780-555-0184</span>
      </div>
      <div class="contact-row">
        <svg viewBox="0 0 16 16"><circle cx="8" cy="8" r="8" fill="#7cc52a"/><rect x="5.5" y="3.5" width="5" height="9" rx="1" fill="#232324"/><rect x="6.3" y="4.6" width="3.4" height="5.6" fill="#7cc52a"/><circle cx="8" cy="11.3" r=".5" fill="#7cc52a"/></svg>
        <span>+1 780-555-0261</span>
      </div>
      <div class="contact-row">
        <svg viewBox="0 0 16 16"><circle cx="8" cy="8" r="8" fill="#7cc52a"/><rect x="4" y="5" width="8" height="6" rx="1" fill="#232324"/><path d="M4.5 5.6 8 8.3l3.5-2.7" stroke="#7cc52a" fill="none" stroke-width=".9"/></svg>
        <span>halya.dorosh@quillmail.example</span>
      </div>
      <div class="contact-row">
        <svg viewBox="0 0 16 16"><circle cx="8" cy="8" r="8" fill="#7cc52a"/><circle cx="8" cy="8" r="4" fill="none" stroke="#232324" stroke-width="1"/><ellipse cx="8" cy="8" rx="1.8" ry="4" fill="none" stroke="#232324" stroke-width="1"/><path d="M4 8h8" stroke="#232324" stroke-width="1"/></svg>
        <span>brovix.example</span>
      </div>
    </div>
  </section>
</main>
</body>
</html>
```